Probate (Legal) Wordpress Design with Coding for Online Company

I need a Wordpress design with coding, pictures, content to be provided by me, fully responsive, and development. This is for a 6-7 page design.

Pages Needed: Home/About/Probate/Process/FAQ/Contact Us/Blog.

The home page should be organized as followed:
-Steps in Probate: Gather; Implement; Close (each step will come with content)
-Flat-Fee Price & Savings: Content will go here with a button to contact us (phone number) or just the phone number.
-You Have Questions, We Have Answers: five questions with content. Only one question answer to show at a time when clicked on the question from the list.
-Get to Know Us: a brief description with content about what we do and who we are.

Main image slogan: Helping Californians deal with loss with DIGNITY & UNDERSTATING (you may use a better slogan if you wish).

The Contact page should not have a map since we are an online company. We service the entire state of California in every county and city.

The About page should be simple, direct, and easy on the eye. It should have a brief description of who we are and it should have no more than 6 reasons why the client should hire us.

About our online California company. We are not attorneys but legal document assistants who prepare legal documents for probate estate when someone dies with or without a will and assets need to be distributed. We have a flat-fee for Formal Probate of $999 and $699 for Informal Probate. We are an online company and offer our services to the entire state of California in every county. We do everything over the phone and email. The turn around time for us to prepare the initial legal paperwork for the client is within 3-5 business days. We can prepare, file, serve and manage a probate matter from petition to closing. We are not attorneys so our prices are very affordable compare to the attorney.

The company name for the website will be www.velmarhollow.com, The Velmar Hollow Group.

I do not have a logo yet. The colors of the website should be easy on the eye and calming. THE SITE SHOULD BE SIMPLE AND STRAIGHT TO THE POINT. EASY TO NAVIGATE.

The company phone number should be very visible and should stand out to the client. It should also be clickable and ready to dial for smartphone users.

I do not want a contact form on the homepage. THE MAIN THING IS FOR THE POTENTIAL CLIENT TO CALL OUR OFFICE TO SIGN UP.

I do like some images of family or people since we are dealing with people who just lost a loved one. Not all the images have to be of people.

The site should not look like we practice law or that people can mistake us for attorneys.

Target Market(s)

People who just lost a loved one who had property, assets, in California but died with or without a will or trust. This is for people looking to hire non-attorneys.

Coding

Coded - Design and coding required

Font styles to use
Serif

Colors

Designer to choose colors to be used in the design.

Requirements
Must have
• Refer to Project Description.
Nice to have
• The sample images provided is what I am attracted to for the homepage image.
Should not have

```html
<!DOCTYPE html>
<html lang="en">
<head>
<meta charset="utf-8">
<title>Process – The Velmar Hollow Group</title>
<link href="https://fonts.googleapis.com/css2?family=Crimson+Text:wght@600;700&family=Open+Sans:wght@400;600;700&display=swap" rel="stylesheet">
<style>
  :root {
    --orange: #f7821a;
    --orange-band: #ad6a1f;
    --teal: #13708f;
    --teal-band: #1c83a5;
    --dark: #474747;
    --text: #3c3c3c;
    --white: #ffffff;
    --line: #2e2e2e;
  }
  * { margin: 0; padding: 0; box-sizing: border-box; }
  html, body { width: 1200px; height: 2284px; overflow: hidden; background: var(--white); }
  body { position: relative; font-family: "Open Sans", Arial, sans-serif; color: var(--text); }
  .abs { position: absolute; }
  .serif { font-family: "Crimson Text", Georgia, serif; }

  .top-rule { left: 0; top: 0; width: 1200px; height: 3px; background: var(--orange); }
  .call-tab { left: 792px; top: 0; width: 297px; height: 43px; background: var(--orange);
    border-radius: 0 0 26px 26px; color: var(--white); font-weight: 700; font-size: 17px;
    display: flex; align-items: center; justify-content: center; gap: 10px; }
  .brand { left: 99px; top: 80px; font-family: "Crimson Text", Georgia, serif; font-weight: 700;
    font-size: 22px; color: var(--teal); letter-spacing: .3px; text-transform: uppercase; }
  .main-nav { left: 457px; top: 77px; width: 650px; height: 24px; }
  .main-nav a { position: absolute; font-size: 15.5px; font-weight: 600; color: #111; text-decoration: none; }

  .hero { left: 0; top: 125px; width: 1200px; height: 192px;
    background: linear-gradient(90deg, #6f6d6a 0%, #807b76 50%, #8b7564 75%, #6e6660 100%); }
  .hero-title { left: 99px; top: 185px; font-size: 56px; font-weight: 700; color: var(--white); }

  .section-title { left: 0; width: 1200px; text-align: center; top: 385px; font-size: 31px; font-weight: 700; color: var(--teal); }
  .title-rule { left: 562px; top: 449px; width: 79px; height: 2px; background: var(--teal); }

  .step-head { font-size: 26px; font-weight: 700; }
  .step-copy { font-size: 14px; line-height: 22px; color: var(--text); }
  .step-gather { left: 99px; top: 545px; width: 310px; text-align: right; }
  .step-gather .step-head { color: var(--orange); }
  .step-close { left: 792px; top: 545px; width: 310px; text-align: left; }
  .step-close .step-head { color: var(--teal); }
  .step-implement { left: 445px; top: 864px; width: 312px; text-align: center; }
  .step-implement .step-head { color: var(--dark); }
  .step-copy { margin-top: 8px; }

  .cycle { left: 0; top: 0; }

  .detail-card { left: 99px; top: 1104px; width: 1002px; height: 305px; background: var(--orange); border-radius: 3px; }
  .detail-card-inner { position: absolute; inset: 9px; border: 2px solid var(--white); border-radius: 3px;
    text-align: center; color: var(--white); padding: 73px 60px 0; }
  .detail-card h3 { font-size: 34px; font-weight: 700; letter-spacing: .5px; }
  .detail-card p { margin-top: 22px; font-size: 13.5px; line-height: 25px; }
  .step-badge { left: 555px; top: 1055px; width: 92px; height: 92px; border-radius: 50%;
    background: var(--dark); border: 4px solid var(--white); color: var(--white);
    font-size: 40px; display: flex; align-items: center; justify-content: center; }

  .band { top: 1497px; width: 600px; height: 488px; }
  .band-left { left: 0; background: linear-gradient(135deg, #1f88aa, #16708f); }
  .band-right { left: 600px; background: linear-gradient(135deg, #b16d21, #99591a); }
  .band-content { top: 1555px; width: 470px; color: var(--white); }
  .band-content h2 { font-size: 33px; font-weight: 600; letter-spacing: .3px; }
  .band-rule { width: 107px; height: 2px; background: var(--white); margin-top: 12px; }
  .band-content p { font-size: 14.5px; line-height: 22px; font-weight: 600; margin-top: 28px; }
  .band-content p + p { margin-top: 22px; }
  .read-more { display: inline-block; margin-top: 40px; border: 2px solid var(--white); color: var(--white);
    font-size: 15px; font-weight: 600; padding: 13px 10px; text-decoration: none; }

  .footer-nav { left: 0; top: 2053px; width: 1200px; text-align: center; font-size: 15px; color: #111; }
  .footer-nav span { margin: 0 18px; }
  .footer-contact { top: 2128px; display: flex; align-items: center; gap: 14px; font-size: 21px; color: #111; }
  .footer-rule { left: 99px; top: 2208px; width: 1002px; height: 2px; background: var(--line); }
  .copyright { left: 0; top: 2235px; width: 1200px; text-align: center; font-size: 14px; font-weight: 600; color: #111; }
</style>
</head>
<body>
  <div class="abs top-rule"></div>
  <div class="abs call-tab">
    <svg width="16" height="16" viewBox="0 0 16 16"><rect width="16" height="16" rx="3" fill="#fff"/><path d="M5 3.5l1.8 2.3-1 1.1c.6 1.3 1.6 2.3 2.9 2.9l1.1-1 2.3 1.8-1 1.9C7.8 12.4 3.6 8.2 3.6 4.5z" fill="#f7821a"/></svg>
    Call Us At: +180 555 0142
  </div>
  <div class="abs brand">The Velmar Hollow Group</div>
  <nav class="abs main-nav">
    <a style="left:0">HOME</a><a style="left:87px">ABOUT</a><a style="left:180px">PROBATE</a>
    <a style="left:289px">PROCESS</a><a style="left:396px">FAQ</a><a style="left:466px">CONTACT US</a><a style="left:602px">BLOG</a>
  </nav>

  <div class="abs hero" role="img" aria-label="Photo of a family group embracing, toned grey"></div>
  <h1 class="abs hero-title serif">PROCESS</h1>

  <h2 class="abs section-title serif">OUR PROCESS</h2>
  <div class="abs title-rule"></div>

  <svg class="abs cycle" width="1200" height="900" viewBox="0 0 1200 900">
    <path d="M465 716 A145 145 0 0 1 601 521" fill="none" stroke="#f7821a" stroke-width="3"/>
    <path d="M601 521 A145 145 0 0 1 737 716" fill="none" stroke="#13708f" stroke-width="3"/>
    <path d="M737 716 A145 145 0 0 1 465 716" fill="none" stroke="#474747" stroke-width="3"/>
    <g font-family="Open Sans, Arial, sans-serif" font-size="27" fill="#fff" text-anchor="middle">
      <circle cx="475" cy="594" r="29" fill="#f7821a" stroke="#fff" stroke-width="3"/>
      <text x="475" y="604">1</text>
      <circle cx="727" cy="594" r="29" fill="#13708f" stroke="#fff" stroke-width="3"/>
      <text x="727" y="604">3</text>
      <circle cx="601" cy="811" r="29" fill="#474747" stroke="#fff" stroke-width="3"/>
      <text x="601" y="821">2</text>
    </g>
  </svg>

  <div class="abs step-gather">
    <div class="step-head serif">Gather:</div>
    <p class="step-copy">Duis aute irure dolor in reprehenderit in vo luptate velit esse cillum dolore eu fugiat nulla pariatur.</p>
  </div>
  <div class="abs step-close">
    <div class="step-head serif">Close:</div>
    <p class="step-copy">Duis aute irure dolor in reprehenderit in vo luptate velit esse cillum dolore eu fugiat nulla pariatur.</p>
  </div>
  <div class="abs step-implement">
    <div class="step-head serif">Implement:</div>
    <p class="step-copy">Duis aute irure dolor in reprehenderit in vo luptate velit esse cillum dolore eu fugiat nulla pariatur.</p>
  </div>

  <div class="abs detail-card">
    <div class="detail-card-inner">
      <h3 class="serif">GATHER</h3>
      <p>Nemo enim ipsam voluptatem quia voluptas sit aspernatur aut odit aut fugit, sed quia consequuntur magni dolores eos qui ratione volup tatem sequi nesciunt. Neque porro quisquam est, qui dolorem ipsum quia dolor sit amet, consectetur, adipisci velit, sed quia non numquam eius modi tempora incidunt ut labore et dolore magnam aliquam quaerat voluptatem. Ut enim ad minima veniam, quis nostrum exercita tionem ullam corporis suscipit .</p>
    </div>
  </div>
  <div class="abs step-badge">1</div>

  <div class="abs band band-left" role="img" aria-label="Photo of hands at a desk with paperwork, teal toned"></div>
  <div class="abs band band-right" role="img" aria-label="Photo of a hand signing a document with a pen, orange toned"></div>
  <div class="abs band-content" style="left:99px">
    <h2 class="serif">WHAT WE DO</h2>
    <div class="band-rule"></div>
    <p>Sed ut perspiciatis unde omnis iste natus error sit voluptatem accu santium doloremque laudantium, totam rem aperiam, eaque ipsa quae ab illo inventore veritatis et quasi architecto beatae.</p>
    <p>Nemo enim ipsam voluptatem quia voluptas sit aspernatur aut odit aut fugit, sed quia consequuntur magni dolores eos qui ratione vo luptatem.</p>
    <a class="read-more">READ MORE</a>
  </div>
  <div class="abs band-content" style="left:632px">
    <h2 class="serif">WHO WE ARE</h2>
    <div class="band-rule"></div>
    <p>Sed ut perspiciatis unde omnis iste natus error sit voluptatem accu santium doloremque laudantium, totam rem aperiam, eaque ipsa quae ab illo inventore veritatis et quasi architecto beatae.</p>
    <p>Nemo enim ipsam voluptatem quia voluptas sit aspernatur aut odit aut fugit, sed quia consequuntur magni dolores eos qui ratione vo luptatem.</p>
    <a class="read-more">READ MORE</a>
  </div>

  <nav class="abs footer-nav">
    HOME<span>|</span>ABOUT<span>|</span>PROBATE<span>|</span>PROCESS<span>|</span>FAQ<span>|</span>CONTACT US<span>|</span>BLOG
  </nav>
  <div class="abs footer-contact" style="left:332px">
    <svg width="46" height="46" viewBox="0 0 46 46"><circle cx="23" cy="23" r="21.5" fill="none" stroke="#111" stroke-width="2"/><path d="M16 13.5l3.2 4-1.7 2c1.1 2.4 2.9 4.2 5.3 5.3l2-1.7 4 3.2-1.8 3.3C20.5 28.6 14 22 13.3 15.3z" fill="#111"/></svg>
    +180 555 0142
  </div>
  <div class="abs footer-contact" style="left:571px">
    <svg width="46" height="46" viewBox="0 0 46 46"><circle cx="23" cy="23" r="21.5" fill="none" stroke="#111" stroke-width="2"/><rect x="13" y="16" width="20" height="14" rx="1.5" fill="none" stroke="#111" stroke-width="2"/><path d="M13.5 17l9.5 7 9.5-7" fill="none" stroke="#111" stroke-width="2"/></svg>
    info@velmarhollow.com
  </div>
  <div class="abs footer-rule"></div>
  <p class="abs copyright">Copyrights @ 2017 The Velmar Hollow Group. All Rights Reserved.</p>
</body>
</html>
```